Bold and colurful E-liquid Design Template

I'm looking for a new label for my house range of vape e-liquids. I currently have almost 40 flavours, so I'm looking for a single label design that I can modify to create the rest of the flavours.
Each label will have the same design, but I'll change the color for each flavour and the name.
I'd like the label to be predominantly text based with bold text and bold colours. I like bold typographic styles. Also for each flavour I'd like to add 1 - 3 letters to represent the flavour. This can be in a larger font.
eg for
Blueberry I'll use the letter B
Pineapple Peach will use PP
Cinnamon Blueberry Muffin uses CBM
The colour used on the label will also be important so they stand out nicely on the shelf.
I've attached a psd mockup of the bottles I'll be using.

```html
<!DOCTYPE html>
<html lang="en">
<head>
<meta charset="utf-8">
<title>CBM E-Liquid Label</title>
<link rel="stylesheet" href="https://fonts.googleapis.com/css2?family=Montserrat:wght@400;800;900&family=Josefin+Sans:wght@600;700&display=swap">
<style>
  :root {
    --backdrop: #e6e7e6;
    --label-white: #fbfbfb;
    --flavour: #9b0039;
    --flavour-deep: #7d002d;
    --gold: #c9a44a;
    --ink: #111111;
    --burst: #f3c9d6;
  }
  html, body {
    margin: 0;
    width: 984px;
    height: 1200px;
    overflow: hidden;
    background: var(--backdrop);
  }
  .label {
    position: absolute;
    left: 292px;
    top: 33px;
    width: 400px;
    height: 1135px;
    box-shadow: 0 6px 24px rgba(0,0,0,0.15);
  }
  .brand-name { font-family: "Montserrat", sans-serif; font-weight: 400; fill: #ffffff; }
  .flavour-code { font-family: "Montserrat", sans-serif; font-weight: 900; fill: var(--flavour); }
  .flavour-name { font-family: "Montserrat", sans-serif; font-weight: 900; fill: var(--ink); }
  .product-type { font-family: "Josefin Sans", sans-serif; font-weight: 700; fill: #ffffff; }
  .strength { font-family: "Josefin Sans", sans-serif; font-weight: 600; fill: var(--ink); }
  .volume { font-family: "Josefin Sans", sans-serif; font-weight: 700; fill: var(--ink); }
</style>
</head>
<body>
<svg class="label" viewBox="0 0 400 1135" xmlns="http://www.w3.org/2000/svg">
  <defs>
    <radialGradient id="burst-glow" cx="0.5" cy="0.5" r="0.6">
      <stop offset="0" stop-color="var(--burst)" stop-opacity="0.9"/>
      <stop offset="1" stop-color="var(--burst)" stop-opacity="0"/>
    </radialGradient>
  </defs>

  <rect class="label-base" x="0" y="0" width="400" height="1135" fill="var(--label-white)"/>

  <g class="top-bands">
    <rect x="0" y="0" width="400" height="7" fill="var(--flavour)"/>
    <rect x="0" y="9" width="400" height="3" fill="var(--gold)"/>
    <rect x="0" y="13" width="400" height="24" fill="var(--flavour)"/>
  </g>

  <rect class="sunburst" x="0" y="140" width="400" height="940" fill="url(#burst-glow)" role="img" aria-label="Faint pink sunburst rays radiating from the flavour name"/>

  <g class="brand">
    <rect x="73" y="92" width="262" height="91" fill="var(--ink)"/>
    <text class="brand-name" x="204" y="160" font-size="48" text-anchor="middle" textLength="228" lengthAdjust="spacingAndGlyphs">LARKSPUR</text>
  </g>

  <text class="flavour-code" x="20" y="390" font-size="215" textLength="365" lengthAdjust="spacingAndGlyphs">CBM</text>

  <g class="flavour-name-block">
    <text class="flavour-name" x="0" y="510" font-size="92" textLength="400" lengthAdjust="spacingAndGlyphs">CINNAMON</text>
    <text class="flavour-name" x="-2" y="582" font-size="92" textLength="404" lengthAdjust="spacingAndGlyphs">BLUEBERRY</text>
    <text class="flavour-name" x="40" y="673" font-size="92" textLength="320" lengthAdjust="spacingAndGlyphs">MUFFIN</text>
  </g>

  <g class="product-type-badge">
    <rect x="40" y="710" width="325" height="122" fill="var(--flavour)"/>
    <text class="product-type" x="72" y="797" font-size="62" textLength="262" lengthAdjust="spacingAndGlyphs">E-LIQUID</text>
  </g>

  <text class="strength" x="57" y="927" font-size="46" textLength="293" lengthAdjust="spacingAndGlyphs">70mg / 30ml</text>
  <rect class="divider" x="50" y="961" width="308" height="4" fill="var(--flavour)"/>
  <text class="volume" x="120" y="1080" font-size="64" textLength="155" lengthAdjust="spacingAndGlyphs">60ml</text>

  <g class="bottom-bands">
    <rect x="0" y="1103" width="400" height="22" fill="var(--flavour)"/>
    <rect x="0" y="1127" width="400" height="3" fill="var(--gold)"/>
    <rect x="0" y="1131" width="400" height="4" fill="var(--flavour)"/>
  </g>
</svg>
</body>
</html>
```